update of B2B website and conversion to single page

The current website needs to be modernized. I want what is commonly called a single page website. It is not actually a single page. See some examples here:
https://www.plivenor.example/
https://www.quorbel.example/
https://www.trindavex.example/
Most or all graphics will be replaced.
Please see the attached spreadsheet for a rough draft of the home page layout. Convert the existing website at https://www.zolvarin.example/ to a single page website. We will provide the page content. You will provide all of the design, graphics, development, production deployment. etc. The look and feel should be corporate, polished, premium.

```html
<!DOCTYPE html>
<html lang="en">
<head>
<meta charset="utf-8">
<title>Zolvarin Data – Data Quality Proof of Concept</title>
<link rel="stylesheet" href="https://fonts.googleapis.com/css2?family=Poppins:wght@300;400;500;600;700&display=swap">
<style>
  :root{
    --brand-blue:#0175a6;
    --brand-blue-deep:#01628f;
    --accent-yellow:#f6c936;
    --ink:#1c1c24;
    --muted:#8a8a92;
    --rule:#e2e2e6;
    --slate:#4c5a94;
    --cloud:#8fb2ff;
    --white:#ffffff;
  }
  *{margin:0;padding:0;box-sizing:border-box}
  html,body{width:1200px;height:1200px;overflow:hidden;background:var(--white)}
  body{position:relative;font-family:"Poppins",sans-serif;color:var(--ink)}
  .hero-band{position:absolute;inset:0;width:1200px;height:1200px}
  .site-header{position:absolute;left:0;top:0;width:1200px;height:90px}
  .brand{position:absolute;left:30px;top:30px;display:flex;align-items:center;gap:10px;
    color:var(--white);font-weight:600;font-size:26px;letter-spacing:-.5px}
  .brand-dot{width:20px;height:20px;border-radius:50%;background:var(--accent-yellow)}
  .main-nav{position:absolute;top:38px;left:0;width:1200px;font-size:11px;font-weight:500;
    letter-spacing:1.2px;color:var(--white)}
  .main-nav span{position:absolute;white-space:nowrap}
  .hero-title{position:absolute;left:70px;top:213px;font-weight:300;font-size:50px;line-height:47px;
    color:var(--accent-yellow);letter-spacing:.5px}
  .hero-lead{position:absolute;left:74px;top:343px;width:460px;color:var(--white);font-size:12.2px;
    line-height:21.5px;letter-spacing:.3px}
  .hero-lead strong{font-weight:700;display:block}
  .btn-outline{position:absolute;left:75px;top:442px;width:121px;height:28px;border:1px solid var(--white);
    color:var(--white);font-size:8px;font-weight:500;letter-spacing:1.2px;display:flex;align-items:center;justify-content:center}
  .hero-art{position:absolute;left:652px;top:198px;width:460px;height:400px;border-radius:48% 52% 40% 46%/50% 45% 55% 50%;
    background:radial-gradient(ellipse at 45% 45%,#e8eefc 0%,#c9d8ff 45%,var(--cloud) 75%,rgba(143,178,255,0) 76%)}
  .feature-card{position:absolute;left:79px;top:661px;width:476px;height:406px;
    background:linear-gradient(120deg,var(--brand-blue-deep) 0%,#0a78a8 55%,#1a8cbc 100%);color:var(--white)}
  .feature-card h2{position:absolute;left:61px;top:98px;font-weight:300;font-size:27px;line-height:28px;letter-spacing:.3px}
  .feature-card p{position:absolute;left:61px;top:185px;width:320px;font-size:10.8px;line-height:16.2px;letter-spacing:.2px}
  .btn-solid{position:absolute;left:61px;top:271px;width:107px;height:29px;background:var(--white);color:var(--brand-blue);
    font-size:8.5px;font-weight:500;letter-spacing:1px;display:flex;align-items:center;justify-content:center}
  .connector{position:absolute;left:606px;width:400px}
  .connector .rule{position:absolute;left:0;top:0;width:66px;height:1px;background:var(--rule)}
  .connector svg{position:absolute;left:74px;top:-9px}
  .connector h3{position:absolute;left:103px;top:-8px;font-size:10.5px;font-weight:500;letter-spacing:1.3px}
  .connector p{position:absolute;left:103px;top:12px;width:290px;font-size:10.6px;line-height:16.3px;color:var(--muted);letter-spacing:.3px}
  .intro-rule{position:absolute;left:0;top:1181px;width:214px;height:1px;background:var(--rule)}
  .intro-title{position:absolute;left:223px;top:1162px;font-size:28px;font-weight:400;letter-spacing:.5px;white-space:nowrap}
  .intro-title em{font-style:normal;color:var(--slate)}
  .intro-arc{position:absolute;left:700px;top:1142px}
</style>
</head>
<body>
<svg class="hero-band" viewBox="0 0 1200 1200" aria-hidden="true">
  <polygon points="0,0 1200,0 1200,308 0,711" fill="var(--brand-blue)"/>
</svg>

<header class="site-header">
  <div class="brand"><span class="brand-dot"></span>Zolvarin Data</div>
  <nav class="main-nav">
    <span style="left:476px">SERVICES</span>
    <span style="left:576px">CONNECTORS</span>
    <span style="left:701px">FEATURES</span>
    <span style="left:799px">WHY QV*PLUS?</span>
    <span style="left:933px">OFFERS</span>
    <span style="left:1024px">BLOG</span>
    <span style="left:1100px">COMPANY</span>
  </nav>
</header>

<h1 class="hero-title">Data Quality Proof<br>of Concept</h1>
<p class="hero-lead"><strong>Find Out Exactly What QV*Plus Can Do For You</strong>Test drive QV*Plus to cleanse data, verify addresses and positively identify duplicate records in your application or database.</p>
<a class="btn-outline">FULL FEATURES</a>

<div class="hero-art" role="img" aria-label="Isometric cloud containing rows of server racks with a person standing beside them"></div>

<section class="feature-card">
  <h2>Enterprise Data Quality<br>Made Easy</h2>
  <p>Cleanse data, verify addresses, find and consolidate duplicate records in batch and real time. Connectors for Orvane E-Business Suite, Saletrove.example and Sorbell</p>
  <a class="btn-solid">READ MORE...</a>
</section>

<div class="connector" style="top:821px">
  <span class="rule"></span>
  <svg width="20" height="20" viewBox="0 0 20 20" fill="none" stroke="#333" stroke-width="1"><rect x="2" y="2" width="16" height="16"/><path d="M6 2v9l2.5-2 2.5 2V2M2 14h16"/></svg>
  <h3>ORVANE</h3>
  <p>QV*Plus has connectors for all of the major SQL/relational databases, including Orvane. The QV*Plus Orvane Database Connector eliminates the</p>
</div>

<div class="connector" style="top:931px">
  <span class="rule"></span>
  <svg width="30" height="26" viewBox="0 0 30 26" fill="none" stroke="#333" stroke-width="1" style="left:70px;top:-12px"><path d="M7 19a6 6 0 0 1 1-12 8 8 0 0 1 15 2 5 5 0 0 1 0 10"/><rect x="10" y="12" width="10" height="12"/><path d="M12 16h6M12 20h6"/></svg>
  <h3>MarlSQL</h3>
  <p>The QV*Plus Veltrix SQL Server Database Connector eliminates the need for custom integration work, saving your business time and</p>
</div>

<span class="intro-rule"></span>
<h2 class="intro-title">We provdide <em>effective</em></h2>
<svg class="intro-arc" width="360" height="60" viewBox="0 0 360 60" aria-hidden="true">
  <path d="M20 60 A180 180 0 0 1 330 60" fill="none" stroke="#ececf0" stroke-width="2"/>
</svg>
</body>
</html>
```